We are a recruitment company based in Norwich/Cambridge England.
I have included our company logo which we want to remain the same.

What we are looking for is a new creative Business card which will really stand out!!

Contact Information for Business Card

Harriet Dunmore
email: Harriet@plavex.co.uk
Address: Brackwell House
Fenmoor Enterprise Park
Partridge Way
Norwich
QB9 3KX
Tel:01632 960418

```html
<!DOCTYPE html>
<html lang="en">
<head>
<meta charset="utf-8">
<title>Plavex Business Card</title>
<link href="https://fonts.googleapis.com/css2?family=Roboto:wght@400;500;700&display=swap" rel="stylesheet">
<style>
  :root {
    --green: #8dc63f;
    --grey: #6d6e71;
    --ink: #4a4a4c;
    --paper: #ffffff;
    --backdrop: #2b2b2d;
  }
  * { margin: 0; padding: 0; box-sizing: border-box; }
  html, body { width: 1200px; height: 960px; overflow: hidden; }
  body {
    background: var(--backdrop);
    font-family: "Roboto", Arial, sans-serif;
    display: flex;
    flex-direction: column;
    align-items: center;
    justify-content: center;
    gap: 60px;
  }
  .card {
    position: relative;
    width: 700px;
    height: 400px;
    overflow: hidden;
  }

  /* Back of card */
  .card--back { background: var(--green); }
  .back-brand {
    position: absolute;
    top: 150px; left: 0; right: 0;
    display: flex;
    align-items: center;
    justify-content: center;
    gap: 22px;
  }
  .back-brand .dot {
    width: 56px; height: 56px;
    border-radius: 50%;
    background: var(--paper);
  }
  .back-brand .name {
    color: var(--paper);
    font-size: 64px;
    font-weight: 700;
    line-height: 1;
  }
  .back-url {
    position: absolute;
    top: 300px; left: 0; right: 0;
    text-align: center;
    color: var(--paper);
    font-size: 14px;
    letter-spacing: 6px;
  }

  /* Front of card */
  .card--front { background: var(--paper); }
  .brand {
    position: absolute;
    top: 60px; right: 50px;
    text-align: right;
  }
  .brand-row {
    display: flex;
    align-items: center;
    justify-content: flex-end;
    gap: 12px;
  }
  .brand-row .dot {
    width: 34px; height: 34px;
    border-radius: 50%;
    background: var(--green);
  }
  .brand-row .name {
    color: var(--grey);
    font-size: 44px;
    font-weight: 700;
    line-height: 1;
  }
  .tagline {
    color: var(--grey);
    font-size: 10px;
    letter-spacing: 2px;
    margin-top: 4px;
  }
  .person {
    position: absolute;
    top: 160px; right: 50px;
    text-align: right;
    text-transform: uppercase;
  }
  .person .full-name {
    color: var(--green);
    font-size: 22px;
    font-weight: 700;
  }
  .person .role {
    color: var(--grey);
    font-size: 18px;
    font-weight: 500;
    margin-top: 2px;
  }
  .contact {
    position: absolute;
    left: 44px; right: 44px;
    top: 262px;
    color: var(--ink);
    font-size: 15px;
    line-height: 1.65;
  }
  .contact .label { color: var(--green); font-weight: 700; }
  .rule {
    position: absolute;
    left: 44px; right: 60px;
    top: 348px;
    height: 2px;
    background: var(--green);
  }
</style>
</head>
<body>
  <section class="card card--back" aria-label="Card back">
    <div class="back-brand">
      <span class="dot"></span>
      <span class="name">Plavex</span>
    </div>
    <p class="back-url">www.plavex.co.uk</p>
  </section>

  <section class="card card--front" aria-label="Card front">
    <div class="brand">
      <div class="brand-row">
        <span class="dot"></span>
        <span class="name">Plavex</span>
      </div>
      <p class="tagline">Technology Recruitment</p>
    </div>
    <div class="person">
      <p class="full-name">Harriet Dunmore</p>
      <p class="role">CEO/Founder</p>
    </div>
    <div class="contact">
      <p>Brackwell House, Fenmoor Enterprise Park, Partridge Way, Norwich QB9 3KX</p>
      <p><span class="label">P.</span> 01632 960418 <span class="label">E.</span> Harriet@plavex.co.uk <span class="label">W.</span> www.plavex.co.uk</p>
    </div>
    <div class="rule"></div>
  </section>
</body>
</html>
```